Independent Financial Advisor Billboard Campaign - Maple Crest Financial

I am a local, independent financial advisor. My company is Maple Crest Financial, located in Charleston, WV. My main source of revenue comes from those nearing or entering retirement that need assistance with financial planning and investment management. Many are looking to rollover their employer retirement plan into an IRA account. I would like a billboard design campaign that focuses on this type of client. Please see our website www.maplecrestfinancial.com for more information.

```html
<!DOCTYPE html>
<html lang="en">
<head>
<meta charset="utf-8">
<title>Maple Crest Financial — Billboard</title>
<link href="https://fonts.googleapis.com/css2?family=Cinzel:wght@500&family=Bebas+Neue&family=Montserrat:wght@400&display=swap" rel="stylesheet">
<style>
  :root {
    --navy: #36527d;
    --paper: #f3f2f1;
    --cyan: #74f0e3;
    --photo-a: rgba(214, 196, 196, 0);
    --photo-b: #c6b6b4;
    --photo-c: #8f8a92;
    --backdrop: #e4e6e9;
    --white: #ffffff;
  }
  * { box-sizing: border-box; margin: 0; padding: 0; }
  html, body { width: 1200px; height: 733px; overflow: hidden; }
  body { background: var(--backdrop); position: relative; }

  .billboard {
    position: absolute;
    left: 20px; top: 190px;
    width: 1160px; height: 352px;
    background: var(--paper);
    overflow: hidden;
  }
  .top-band {
    position: absolute; left: 0; top: 0;
    width: 100%; height: 28px;
    background: var(--navy);
  }
  .photo-area {
    position: absolute; right: 0; top: 28px; bottom: 0;
    width: 340px;
    background: linear-gradient(90deg, var(--photo-a) 0%, var(--photo-b) 35%, var(--photo-c) 100%);
  }
  .brand {
    position: absolute; left: 36px; top: 70px;
    display: flex; align-items: center; gap: 34px;
  }
  .brand-square {
    width: 150px; height: 150px;
    background: var(--navy);
  }
  .brand-name {
    font-family: "Cinzel", serif;
    font-weight: 500;
    color: var(--navy);
    line-height: 1;
    white-space: nowrap;
  }
  .brand-name .line-main { display: block; font-size: 72px; }
  .brand-name .line-sub {
    display: block; font-size: 34px; letter-spacing: 0.62em;
    margin-top: 22px; padding-left: 128px;
  }
  .divider {
    position: absolute; left: 972px; top: 98px;
    width: 3px; height: 180px;
    background: var(--navy);
  }
  .services {
    position: absolute; left: 990px; top: 96px;
    list-style: none;
    font-family: "Bebas Neue", sans-serif;
    font-size: 24px; line-height: 36px;
    letter-spacing: 0.01em;
    white-space: nowrap;
    color: var(--cyan);
  }
  .contact-band {
    position: absolute; left: 0; bottom: 0;
    width: 1000px; height: 62px;
    background: var(--navy);
    border-top-right-radius: 34px;
    display: flex; align-items: center;
    padding-left: 36px;
    font-family: "Montserrat", sans-serif;
    font-size: 17px; letter-spacing: 0.02em;
    white-space: nowrap;
    color: var(--white);
  }
  .contact-band .tagline { font-size: 19px; letter-spacing: 0.05em; margin-right: 8px; }
</style>
</head>
<body>
  <section class="billboard">
    <div class="top-band"></div>
    <div class="photo-area" role="img" aria-label="Photo of a smiling retired couple embracing"></div>

    <div class="brand">
      <div class="brand-square"></div>
      <p class="brand-name">
        <span class="line-main">Maple Crest</span>
        <span class="line-sub">Financial</span>
      </p>
    </div>

    <div class="divider"></div>
    <ul class="services">
      <li>Financial Advice</li>
      <li>Financial Planing</li>
      <li>Investments</li>
      <li>Insurance</li>
      <li>Employer Plans</li>
    </ul>

    <div class="contact-band">
      <span class="tagline">YOUR FINANCIAL FUTURE/</span>
      <span class="web">www.maplecrestfinancial.com/ contact@maplecrestfinancial.com</span>
    </div>
  </section>
</body>
</html>
```